Deodorant Product Sales One Pager and Annexes

Schedule: Very short deadline - to be complete within 12 hours
Budget: 2-3 hours
Format: Adobe Illustrator / A4 landscape or portrait - for submission by email in PDF
OBJECTIVE
We need a one pager sales sheet and its annexes to present a new deodorant range to the largest supermarket chain in Australia. This is a very important submission that can create more design projects for you. Please refer to the attachments for a starting point. We need to keep the design minimalist and elegant, stylish, clean and chic IN KEEPING WITH THE 1.618 ratio. Styles to avoid are too bright colors, clutter, comic or gimmicky styles. Please maintain a sense of high quality design and professionalism as this is a premium product in Australia.
TARGET AUDIENCE
Senior buyer of largest supermarket chain in Australia
Attachments:
Product one pager
Annexes to one pager
Product shots in low and high resolution
Target Market(s)
Senior cosmetics buyer at Australia's largest supermarket chain
Industry/Entity Type
Landscape

```html
<!DOCTYPE html>
<html lang="en">
<head>
<meta charset="utf-8">
<title>Velora – The Magnesium Trend</title>
<link rel="stylesheet" href="https://fonts.googleapis.com/css2?family=Zilla+Slab:ital,wght@0,700;1,400;1,600;1,700&family=Archivo:wght@400;500&display=swap">
<style>
  :root {
    --paper: #ffffff;
    --slate-panel: #6b7b87;
    --ink-heading: #3c4853;
    --ink-body: #5f6f7b;
    --chart-line: #2f6fd6;
    --chart-grid: #e6e9ec;
    --chart-label: #8a949c;
    --white: #ffffff;
  }
  * { margin: 0; padding: 0; box-sizing: border-box; }
  html, body { width: 1200px; height: 851px; overflow: hidden; background: var(--paper); }
  .sheet { position: relative; width: 1200px; height: 851px; background: var(--paper); }

  .sidebar { position: absolute; left: 0; top: 0; width: 200px; height: 851px; }
  .product-photo {
    position: absolute; left: 0; top: 0; width: 200px; height: 353px;
    background: radial-gradient(ellipse at 45% 42%, #3a3d40 0 22%, #8d9196 34%, #eef0f1 52%, #ffffff 70%);
  }
  .brand-panel {
    position: absolute; left: 0; top: 353px; width: 200px; height: 498px;
    background: var(--slate-panel); color: var(--white);
  }
  .brand-name {
    position: absolute; left: 28px; top: 52px;
    font-family: "Zilla Slab", serif; font-weight: 700; font-size: 28px; letter-spacing: 0.5px;
  }
  .contact {
    position: absolute; left: 28px; font-family: "Archivo", sans-serif;
    font-size: 10px; line-height: 12.5px; font-weight: 500;
  }
  .contact--address { top: 335px; }
  .contact--lines { top: 404px; }

  .content { position: absolute; left: 425px; top: 182px; width: 546px; }
  .section-title {
    font-family: "Zilla Slab", serif; font-style: italic; font-weight: 700;
    font-size: 17px; color: var(--ink-heading);
  }
  .trend-quote {
    margin-top: 23px; font-family: "Zilla Slab", serif; font-style: italic; font-weight: 400;
    font-size: 14px; line-height: 22px; color: var(--ink-body); text-align: justify;
  }
  .search-chart { display: block; margin-top: 24px; margin-left: 7px; }
  .chart-caption {
    margin-top: 38px; font-family: "Zilla Slab", serif; font-style: italic; font-weight: 600;
    font-size: 15px; color: var(--ink-body);
  }
  .chart-text { font-family: "Archivo", sans-serif; fill: var(--chart-label); }
</style>
</head>
<body>
<main class="sheet">
  <aside class="sidebar">
    <div class="product-photo" role="img" aria-label="Product photo: three dark magnesium deodorant cans with white caps on a white background"></div>
    <div class="brand-panel">
      <div class="brand-name">Velora</div>
      <p class="contact contact--address">abn 12 345 678 901<br>suite 12, 40 Linden St<br>Hawthorn VIC<br>Australia 3122</p>
      <p class="contact contact--lines">t. 0400 000 123<br>f. 03 9000 0456<br>e. hello@velora.com.au<br>www.velora.com.au</p>
    </div>
  </aside>

  <section class="content">
    <h1 class="section-title">The Magnesium Trend</h1>
    <p class="trend-quote">‘Growing consumer awareness of their own deficiencies, its health benefits, and the emergence of innovative forms are making magnesium the hottest ingredient in the mineral category.’ ‘With between 70 and 80% of the population not meeting their recommended intakes of magnesium, consumers – and the health care professionals who advise them – are waking up to the importance of the mineral.’ (Mineral Trade Review, January 2013)</p>

    <svg class="search-chart" width="522" height="226" viewBox="0 0 522 226" role="img" aria-label="Line chart of search interest for magnesium deficiency in Australia, July 2007 to May 2013, rising roughly threefold">
      <text class="chart-text" x="2" y="14" font-size="9">Web Search Interest: <tspan fill="#3c4853">magnesium deficiency</tspan>. Australia, Jul 2007 – May 2013</text>
      <rect x="470" y="2" width="46" height="18" rx="2" fill="none" stroke="#d7dbdf"/>
      <circle cx="488" cy="11" r="3.5" fill="none" stroke="#6b7b87" stroke-width="1.6"/>
      <path d="M503 9 l3 4 l3 -4z" fill="#6b7b87"/>
      <line x1="0" y1="28" x2="522" y2="28" stroke="#eceef0"/>
      <text class="chart-text" x="2" y="50" font-size="10" fill="#3c4853" style="fill:#3c4853">Interest over time</text>
      <text class="chart-text" x="2" y="63" font-size="7">The number 100 represents the peak search interest</text>
      <rect x="382" y="55" width="7" height="7" fill="none" stroke="#c5cacf"/>
      <text class="chart-text" x="393" y="62" font-size="7.5">News headlines</text>
      <text class="chart-text" x="474" y="62" font-size="7.5">Forecast</text>
      <g stroke="var(--chart-grid)" stroke-width="1">
        <line x1="0" y1="95" x2="522" y2="95"/>
        <line x1="0" y1="125" x2="522" y2="125"/>
        <line x1="0" y1="155" x2="522" y2="155"/>
        <line x1="0" y1="185" x2="522" y2="185"/>
        <line x1="0" y1="215" x2="522" y2="215"/>
      </g>
      <g class="chart-text" font-size="6">
        <text x="2" y="93">100</text><text x="2" y="123">80</text><text x="2" y="153">60</text><text x="2" y="183">40</text><text x="2" y="213">20</text>
      </g>
      <polyline fill="none" stroke="var(--chart-line)" stroke-width="1.4" stroke-linejoin="round"
        points="5,203 13.7,161 22.4,167 31.1,155 39.8,149 48.5,157.4 57.2,169.4 65.9,149 74.6,155 83.3,167 92,161 100.7,152.6 109.4,162.2 118.1,140.6 126.8,167 135.5,159.8 144.2,169.4 152.9,149 161.6,152.6 170.3,145.4 179,133.4 187.7,126.2 196.4,131 205.1,121.4 213.8,119 222.5,140.6 231.2,107 239.9,113 248.6,95 257.3,109.4 266,111.8 274.7,97.4 283.4,114.2 292.1,116.6 300.8,116.6 309.5,119 318.2,104.6 326.9,111.8 335.6,123.8 344.3,109.4 353,121.4 361.7,126.2 370.4,128.6 379.1,119 387.8,126.2 396.5,121.4 405.2,107 413.9,103.4 422.6,126.2 431.3,126.2 440,119 448.7,131 457.4,123.8 466.1,128.6 474.8,133.4 483.5,116.6 492.2,111.8 500.9,135.8 509.6,143 518.3,114.2"/>
      <text class="chart-text" x="300" y="209" font-size="7" style="fill:#3c4853">Note</text>
      <g class="chart-text" font-size="6">
        <text x="14" y="224">Jan 2008</text><text x="100" y="224">Jan 2009</text><text x="186" y="224">Jan 2010</text><text x="272" y="224">Jan 2011</text><text x="358" y="224">Jan 2012</text><text x="444" y="224">Jan 2013</text>
      </g>
    </svg>

    <p class="chart-caption">Online search interest for magnesium deficiency increases by 200%</p>
  </section>
</main>
</body>
</html>
```